Elegant Business Card for Technology Company

Client is a supplier of innovative industrial communications and automation equipment since 2002. This contest is to gather fresh ideas for a redesign of the existing business card. Client is looking for design that best communicates tagline "Industrial Networking and Computing Specialist".

Design submissions should look modern, clean, elegant and professional. It should not be cluttered. Use white as the primary colour. Orange and black as secondary colour. Refer to jpeg File 1 on the current design.

Fonts used by Client used include Arial Regular, Arial Black, Roboto Regular, Roboto Black and Lato.

The winning design will be sent for offset printing using super white 250gsm artcard paper (open for suggestions).

Target Market(s)

System Engineers, Project Managers, Purchasing Managers from companies providing engineering services for Smart Cities.

Industry/Entity Type

Information Technology

Contact Information for Business Card

Refer to PDF File 3 for Business Card Details. Priority of short contact information would be as follows Name > Job Title > Email > Mobile > Web > Tel > Fax > Business Address >UEN (UEN represents company registration number)

Font styles to use
Sans Serif

Colors
ffffff
f37122
000000
5c5c5c

Requirements
Must have
• Refer to AI File 2 (Company Logo) & PDF File 3 (Information on Namecard)
Should not have
• No QR codes
• No Social Media Icons
• Do not create full Black or Orange colour background

```html
<!DOCTYPE html>
<html lang="en">
<head>
<meta charset="utf-8">
<title>KELNET Business Card</title>
<link rel="stylesheet" href="https://fonts.googleapis.com/css2?family=Source+Sans+3:wght@400;600;700&display=swap">
<style>
  :root {
    --stage: #3a3633;
    --card: #ffffff;
    --black: #000000;
    --orange: #f37122;
    --grey: #5c5c5c;
    --rule: #c4c4c4;
  }
  * { box-sizing: border-box; margin: 0; padding: 0; }
  html, body {
    width: 1200px; height: 814px; overflow: hidden;
    background: var(--stage);
    font-family: "Source Sans 3", Arial, sans-serif;
  }
  .stage {
    width: 1200px; height: 814px;
    display: flex; align-items: center; justify-content: center; gap: 48px;
  }
  .card {
    position: relative;
    width: 540px; height: 310px;
    background: var(--card);
    color: var(--black);
    box-shadow: 0 10px 28px rgba(0,0,0,.45);
  }
  .wordmark { display: flex; align-items: center; gap: 12px; }
  .wordmark-dot {
    width: 44px; height: 44px; border-radius: 50%;
    background: var(--orange);
  }
  .wordmark-name {
    font-weight: 700; font-size: 40px; letter-spacing: 1px;
    color: var(--black); line-height: 1;
  }
  /* Front */
  .card-front .wordmark { position: absolute; left: 96px; top: 62px; }
  .identity {
    position: absolute; right: 292px; top: 150px;
    text-align: right; line-height: 1.28; font-size: 15px; color: var(--grey);
  }
  .identity .person-name { color: var(--orange); font-size: 21px; font-weight: 600; }
  .identity .person-title { color: var(--black); }
  .divider {
    position: absolute; left: 262px; top: 120px;
    width: 1px; height: 150px; background: var(--rule);
  }
  .contacts {
    position: absolute; left: 280px; top: 122px;
    list-style: none; font-size: 15px; line-height: 1; color: var(--grey);
  }
  .contacts li { display: flex; align-items: center; gap: 10px; height: 22px; }
  .contacts svg { width: 13px; height: 13px; fill: var(--orange); flex: none; }
  /* Back */
  .card-back .wordmark { position: absolute; left: 50%; top: 72px; transform: translateX(-50%); }
  .tagline {
    position: absolute; left: 0; right: 0; top: 150px;
    text-align: center; font-size: 15px; line-height: 1.4; list-style: none;
    color: var(--grey);
  }
  .tagline .tagline-lead { color: var(--black); font-weight: 600; }
</style>
</head>
<body>
<main class="stage">
  <section class="card card-front" aria-label="Business card front">
    <div class="wordmark">
      <span class="wordmark-dot"></span>
      <span class="wordmark-name">KELNET</span>
    </div>
    <div class="identity">
      <p class="person-name">Daniel Koh</p>
      <p class="person-title">Sales Manager</p>
      <p>22 Kallor Road</p>
      <p>Linkpark #04-12 (Block B)</p>
      <p>Singapore 418221</p>
    </div>
    <span class="divider"></span>
    <ul class="contacts">
      <li><svg viewBox="0 0 16 16" aria-hidden="true"><path d="M3 1l3 3-2 2c1 2 3 4 6 6l2-2 3 3-2 2C7 15 1 9 1 3z"/></svg>+65 6100 2040</li>
      <li><svg viewBox="0 0 16 16" aria-hidden="true"><path d="M4 0h8v16H4zM5.5 2v10h5V2z"/></svg>+65 9100 3050</li>
      <li><svg viewBox="0 0 16 16" aria-hidden="true"><path d="M4 1h7v4H4zM1 6h14v7h-3v2H4v-2H1zM5 10v4h6v-4z"/></svg>+65 6100 2041</li>
      <li><svg viewBox="0 0 16 16" aria-hidden="true"><path d="M0 3h16v10H0zM1.5 4.5L8 9l6.5-4.5z"/></svg>sales@kelnet.com.sg</li>
      <li><svg viewBox="0 0 16 16" aria-hidden="true"><circle cx="8" cy="8" r="8"/></svg>www.kelnet.com.sg</li>
    </ul>
  </section>

  <section class="card card-back" aria-label="Business card back">
    <div class="wordmark">
      <span class="wordmark-dot"></span>
      <span class="wordmark-name">KELNET</span>
    </div>
    <ul class="tagline">
      <li class="tagline-lead">Industrial Networking &amp; Computing Specialist</li>
      <li>Industrial Ethernet / Wireless / Cellular</li>
      <li>Industrial &amp; Embedded Computing / Serial / Fieldbus Connectivity</li>
      <li>IP Video Surveillance / Remote Automation</li>
    </ul>
  </section>
</main>
</body>
</html>
```